Wandering Rooms Stationary Set

Wandering Rooms is a bespoke interior design firm set to provide services to VIP clients with elegance and minimalism is the main theme for our stationary set. We require a full stationary set covering A4 letterhead, A4 & A3 envelopes, business cards, USB's, CDs, email signature and any other item the designer sees fit. logo is already designed and finalized, and we require the designer to use it as is without modifying the logo.

Address to be used on letterhead / business cards ...etc shall be as follows:

Phone : +971 2 518 2047
P.O. Box : 309186
Address: Block C&D, Bldg. 47, Court 12, Abu Dhabi, United Arab Emirates
Website: www.wanderingrooms-example.com

Target Market(s)

VIP Clients

Industry/Entity Type

Interior Design

Font styles to use
Other font styles liked:
• something to be unique

Colors

Designer to choose colors to be used in the design.

Requirements
Must have
• Elegant, minimalistic
Nice to have
• Simple yet elegant design having a sharp yet clean cut format
Should not have
• No additional colours, just colours that are used in the logo (silver, black or gold)

```html
<!DOCTYPE html>
<html lang="en">
<head>
<meta charset="utf-8">
<title>Wandering Rooms – Business Card</title>
<link href="https://fonts.googleapis.com/css2?family=Cormorant+Garamond:wght@400;500&family=Great+Vibes&display=swap" rel="stylesheet">
<style>
  :root {
    --backdrop: #1e1e1e;
    --card: #2a2a2a;
    --card-edge: #333333;
    --gold: #c6a45a;
    --silver: #b9b9b9;
    --ink-soft: #a8a8a8;
  }
  html, body {
    margin: 0;
    width: 1200px;
    height: 800px;
    overflow: hidden;
    background: var(--backdrop);
  }
  .stage {
    position: relative;
    width: 1200px;
    height: 800px;
  }
  .card {
    position: absolute;
    top: 245px;
    width: 550px;
    height: 310px;
    background: var(--card);
    border: 1px solid var(--card-edge);
    box-sizing: border-box;
    font-family: "Cormorant Garamond", serif;
  }
  .card--front { left: 35px; }
  .card--back  { left: 615px; }

  .brand-name {
    margin: 0;
    font-family: "Cormorant Garamond", serif;
    font-weight: 400;
    letter-spacing: 0.22em;
    text-transform: uppercase;
    white-space: nowrap;
  }
  .card--front .brand-name {
    position: absolute;
    top: 50%;
    left: 0;
    right: 0;
    transform: translateY(-50%);
    text-align: center;
    font-size: 34px;
    color: var(--silver);
  }
  .card--back .brand-name {
    position: absolute;
    top: 40px;
    right: 32px;
    font-size: 22px;
    color: var(--gold);
  }

  .holder {
    position: absolute;
    top: 104px;
    left: 32px;
  }
  .holder__name {
    margin: 0;
    font-family: "Great Vibes", cursive;
    font-size: 30px;
    color: var(--gold);
    line-height: 1;
  }
  .holder__role {
    margin: 4px 0 0;
    font-size: 15px;
    color: var(--ink-soft);
  }

  .address {
    position: absolute;
    left: 32px;
    bottom: 60px;
    margin: 0;
    font-style: normal;
    font-size: 12px;
    line-height: 1.35;
    color: var(--ink-soft);
  }
  .rule {
    position: absolute;
    left: 32px;
    right: 32px;
    bottom: 46px;
    height: 1px;
    background: var(--gold);
    opacity: 0.7;
  }
  .contacts {
    position: absolute;
    left: 32px;
    right: 32px;
    bottom: 20px;
    display: flex;
    justify-content: space-between;
    font-size: 11.5px;
    line-height: 1.2;
    white-space: nowrap;
    color: var(--ink-soft);
  }
  .contacts__label {
    color: var(--gold);
    font-weight: 500;
    margin-right: 4px;
  }
</style>
</head>
<body>
<main class="stage">
  <section class="card card--front" aria-label="Business card front">
    <p class="brand-name">Wandering Rooms</p>
  </section>

  <section class="card card--back" aria-label="Business card back">
    <p class="brand-name">Wandering Rooms</p>

    <div class="holder">
      <p class="holder__name">Daniel Hart</p>
      <p class="holder__role">President</p>
    </div>

    <address class="address">
      P.O. Box : 309186<br>
      Block C&amp;D, Bldg. 47, Court 12<br>
      Abu Dhabi, United Arab Emirates
    </address>

    <div class="rule"></div>

    <div class="contacts">
      <span><span class="contacts__label">P :</span>+971 2 518 2047</span>
      <span><span class="contacts__label">E :</span>info@wanderingrooms-example.com</span>
      <span><span class="contacts__label">W :</span>www.wanderingrooms-example.com</span>
    </div>
  </section>
</main>
</body>
</html>
```